Business Card Design

We provide services doing multiple jobs in the construction industry.Please note: The company name needs to be ROCK SOLID BUILDING SERVICESAttached logo was an example of what we wanted. Can you change up the colors?

Industry/Entity Type

Construction

Contact Information for Business Card

ROCK SOLID BUILDING SERVICES5401 HUDSON BEND RDAUSTIN, TX 78734(512)243-6854ROCKSOLIDBUILDINGSERVICES@GMAIL.COM

```html
<!DOCTYPE html>
<html lang="en">
<head>
<meta charset="utf-8">
<title>Pearlwood Framing Works — Business Card</title>
<link href="https://fonts.googleapis.com/css2?family=Ubuntu:wght@500;700&family=Marcellus&display=swap" rel="stylesheet">
<style>
  :root {
    --stage: #e9e6e1;
    --card: #ffffff;
    --card-shade: #eef0f3;
    --navy: #2b2577;
    --navy-soft: #4a4391;
    --band: #0d0f24;
  }
  * { margin: 0; padding: 0; box-sizing: border-box; }
  html, body { width: 1200px; height: 858px; overflow: hidden; }
  body {
    background: var(--stage);
    display: flex;
    align-items: center;
    justify-content: center;
    gap: 70px;
  }
  .card {
    background: linear-gradient(150deg, var(--card) 40%, var(--card-shade));
    box-shadow: 0 2px 0 #d6d6d6, 0 4px 0 #cfcfcf, 0 14px 30px rgba(0,0,0,.18);
    position: relative;
    overflow: hidden;
  }
  /* Front */
  .card-front {
    width: 560px;
    height: 320px;
    display: flex;
    flex-direction: column;
    justify-content: center;
    padding-left: 90px;
    font-family: "Ubuntu", sans-serif;
    color: var(--navy);
  }
  .front-name {
    font-size: 68px;
    font-weight: 700;
    letter-spacing: -1px;
    line-height: 1;
  }
  .front-sub {
    font-size: 38px;
    font-weight: 500;
    color: var(--navy-soft);
    margin-top: 10px;
    padding-left: 40px;
  }
  /* Back */
  .card-back {
    width: 320px;
    height: 560px;
    font-family: "Marcellus", serif;
    color: var(--navy);
    text-align: center;
  }
  .brand-mark {
    margin: 70px auto 0;
    display: flex;
    align-items: center;
    justify-content: center;
    gap: 10px;
    font-size: 22px;
    letter-spacing: 1px;
  }
  .brand-mark .square {
    width: 18px; height: 18px;
    background: var(--navy);
  }
  .back-name {
    margin-top: 90px;
    font-size: 30px;
    letter-spacing: 1px;
    line-height: 1.1;
  }
  .back-sub {
    font-size: 20px;
    letter-spacing: 1px;
  }
  .contact {
    position: absolute;
    left: 0; right: 0;
    bottom: 110px;
    font-size: 13px;
    line-height: 1.45;
  }
  .contact .phone { font-size: 15px; }
  .band {
    position: absolute;
    left: 0; right: 0; bottom: 0;
    height: 52px;
    background: var(--band);
  }
</style>
</head>
<body>
  <section class="card card-front">
    <div class="front-name">PEARLWOOD</div>
    <div class="front-sub">FRAMING WORKS</div>
  </section>

  <section class="card card-back">
    <div class="brand-mark"><span class="square"></span>PEARLWOOD FRAMING WORKS</div>
    <div class="back-name">PEARLWOOD</div>
    <div class="back-sub">FRAMING WORKS</div>
    <div class="contact">
      <div class="phone">(512)555-0193</div>
      <div>pearlwoodframingworks@mailnest.example</div>
      <div>7732 Fernglen Pass LN Austin, TX 78734</div>
    </div>
    <div class="band"></div>
  </section>
</body>
</html>
```